Business Cards for new orthopaedic surgery practice

My husband and I are starting our own orthopaedic surgery practice. We are looking for a business card that is uniform, but one will have my name/title and the other will have his. You can just create one design with my name on it for now. But when I choose your design as the winning design I will ask that you add another copy with his name/title.

We are looking for classy, simple, elite all in one. We like dark blues/a little gold/yellow. Something that goes with our logo. We want our logo incorporated. Here is all the info you need:
Business name: RV Bone & Vitality Center
Location: 38517 North Willowmere Ave
Brightwater Cove, FL 33990
Phone: 954-218-4063
Fax: 954-582-7341
Email: info@myrvbonecare.example

Names: Lydia Vance, M.D.
Board Certified Hand and Upper Extremity Surgeon

Ebo Dansu, M.D.
Board Certified Hip & Knee Replacement/General Orthopaedic Surgeon

Can decide what you want to put on the back. Maybe a slogan:
Steady Hands. Lasting Strength.

I am just going to upload our logo. The only thing is if we select you as the winning design, the location, and phone numbers may change. We will need your help to update that once fully solidified.

Industry/Entity Type

Medical

Contact Information for Business Card

Colors
0054AA
0677BA
7BADD7
CADEEF
E8F1F8
0094D4
00A9DD
6FCCEA
C7EBF8
E9F6FB

Requirements
Must have
• class, appeal,
Should not have
• We want to air on the side of masculine if we are looking at masculine vs. feminine feel. But we still want it classy, sophisticated, and something we will love

```html
<!DOCTYPE html>
<html lang="en">
<head>
<meta charset="utf-8">
<title>RV Bone &amp; Vitality Center – Business Card</title>
<link href="https://fonts.googleapis.com/css2?family=Montserrat:wght@400;500;600;700&display=swap" rel="stylesheet">
<style>
  :root {
    --backdrop: #b9b9b9;
    --card-navy: #1b2a50;
    --gold: #c9a45c;
    --white: #ffffff;
    --soft-white: #e9edf5;
  }
  * { box-sizing: border-box; margin: 0; padding: 0; }
  html, body { width: 1200px; height: 802px; overflow: hidden; }
  body {
    background: var(--backdrop);
    font-family: "Montserrat", Arial, sans-serif;
    position: relative;
  }
  .card {
    position: absolute;
    width: 540px;
    height: 310px;
    background: var(--card-navy);
    border-radius: 22px;
    color: var(--white);
    box-shadow: 0 14px 30px rgba(0,0,0,0.28);
  }
  .card--front { left: 40px; top: 246px; }
  .card--back { left: 620px; top: 246px; }

  /* brand lockup */
  .brand {
    position: absolute;
    display: flex;
    align-items: center;
    gap: 12px;
  }
  .brand__ring {
    width: 38px; height: 38px;
    border: 2px solid var(--gold);
    border-radius: 50%;
    flex: none;
  }
  .brand__name {
    font-weight: 600;
    color: var(--white);
    line-height: 1.2;
    letter-spacing: 0.04em;
    text-transform: uppercase;
  }
  .card--front .brand { left: 50%; top: 46px; transform: translateX(-50%); }
  .card--front .brand__name { font-size: 15px; width: 150px; }

  .card--back .brand { left: 50%; top: 92px; transform: translateX(-50%); gap: 16px; }
  .card--back .brand__ring { width: 54px; height: 54px; }
  .card--back .brand__name { font-size: 20px; width: 200px; }

  /* front details */
  .doctor {
    position: absolute;
    left: 0; right: 0; top: 140px;
    text-align: center;
  }
  .doctor__name {
    color: var(--gold);
    font-weight: 700;
    font-size: 22px;
    letter-spacing: 0.02em;
    text-transform: uppercase;
  }
  .doctor__title {
    margin-top: 4px;
    font-size: 13px;
    font-weight: 400;
    color: var(--soft-white);
  }
  .divider {
    position: absolute;
    left: 34px; right: 34px; top: 208px;
    height: 1px;
    background: var(--gold);
  }
  .contacts {
    position: absolute;
    left: 40px; top: 226px;
    list-style: none;
    font-size: 13px;
    line-height: 21px;
  }
  .contacts li { display: flex; align-items: center; gap: 9px; }
  .contacts svg { width: 12px; height: 12px; fill: var(--gold); flex: none; }
  .address {
    position: absolute;
    right: 40px; top: 236px;
    text-align: right;
    font-size: 13px;
    line-height: 21px;
    font-style: normal;
  }

  /* back */
  .slogan {
    position: absolute;
    left: 0; right: 0; bottom: 50px;
    text-align: center;
    color: var(--gold);
    font-weight: 600;
    font-size: 19px;
    letter-spacing: 0.01em;
  }
</style>
</head>
<body>

<section class="card card--front" aria-label="Business card front">
  <div class="brand">
    <span class="brand__ring"></span>
    <span class="brand__name">RV Bone &amp; Vitality Center</span>
  </div>

  <div class="doctor">
    <p class="doctor__name">Lydia Vance, M.D.</p>
    <p class="doctor__title">Board Certified Hand and Upper Extremity Surgeon</p>
  </div>

  <div class="divider"></div>

  <ul class="contacts">
    <li>
      <svg viewBox="0 0 24 24" aria-hidden="true"><path d="M6.6 10.8a15.1 15.1 0 0 0 6.6 6.6l2.2-2.2a1 1 0 0 1 1-.25 11.4 11.4 0 0 0 3.6.57 1 1 0 0 1 1 1V20a1 1 0 0 1-1 1A17 17 0 0 1 3 4a1 1 0 0 1 1-1h3.5a1 1 0 0 1 1 1c0 1.25.2 2.45.57 3.57a1 1 0 0 1-.25 1z"/></svg>
      954-218-4063
    </li>
    <li>
      <svg viewBox="0 0 24 24" aria-hidden="true"><path d="M6 2h10l2 2v5H6zM4 10h16a2 2 0 0 1 2 2v6h-4v4H6v-4H2v-6a2 2 0 0 1 2-2zm4 7v3h8v-3z"/></svg>
      954-582-7341
    </li>
    <li>
      <svg viewBox="0 0 24 24" aria-hidden="true"><path d="M2 5h20v14H2zm2 2v.4l8 5.2 8-5.2V7z"/></svg>
      info@myrvbonecare.example
    </li>
  </ul>

  <address class="address">
    38517 North Willowmere Ave<br>
    Brightwater Cove, FL 33990
  </address>
</section>

<section class="card card--back" aria-label="Business card back">
  <div class="brand">
    <span class="brand__ring"></span>
    <span class="brand__name">RV Bone &amp; Vitality Center</span>
  </div>
  <p class="slogan">Steady Hands. Lasting Strength.</p>
</section>

</body>
</html>
```